Flyer Promoting Careway Benefit Program

I want to promote a Careway Benefit Program to my patients that do not have dental insurance. This flyer would be posted in our waiting room and where people make payments. The goal would be to get those interested to request more information and enroll in the program. I have a card that will be issued that has a logo. Theflyer and card should feel congruent. I've uploaded a file with a copy of that card.
The plan costs $290/person. It includes 2 cleanings, exams, and x-rays. It also includes a 20% discount off of our standard fees. The plan or membership lasts for one year. It is only available to those without insurance. It is also important to let people know that this is not insurance (some kind of a disclaimer).
Updates
This plan is only available to patients at my office. The contact information is: Harborview Dental, 2718 West 4600 North Suite 209, Salt Lake City, Utah 84157. (801) 563-9071. info@harborviewdental-example.com. It is not necessary to include contact information as this flyer will be used as in-office promotion.
Target Market(s)
Those without dental insurance, but have resources to afford dental care.
Industry/Entity Type
Insurance
Look and feel
Each slider illustrates characteristics of the customer's brand and the style your logo design should communicate.

```html
<!DOCTYPE html>
<html lang="en">
<head>
<meta charset="utf-8">
<title>Careway Benefit Program Flyer</title>
<link href="https://fonts.googleapis.com/css2?family=Arimo:wght@400;700&family=Roboto+Condensed:wght@700&display=swap" rel="stylesheet">
<style>
  :root {
    --green: #6ab43e;
    --green-light: #9ad46a;
    --green-dark: #4f9a2c;
    --charcoal: #4a4a4c;
    --ink: #2b2b2b;
    --grey: #6d6e70;
    --yellow: #f7e400;
    --white: #ffffff;
    --paper: #f4f4f4;
  }
  * { margin: 0; padding: 0; box-sizing: border-box; }
  html, body { width: 927px; height: 1200px; overflow: hidden; background: var(--white); }
  .flyer {
    position: relative; width: 927px; height: 1200px; overflow: hidden;
    background: linear-gradient(180deg, var(--white) 0%, var(--paper) 100%);
    font-family: "Arimo", Arial, sans-serif; color: var(--ink);
  }
  .family-photo {
    position: absolute; left: 0; top: 260px; width: 660px; height: 800px;
    background: radial-gradient(ellipse 58% 55% at 40% 55%, #d6b094 0%, #e6cdb9 40%, #eceef2 72%, rgba(244,244,244,0) 100%);
  }
  .contact-tab {
    position: absolute; right: 0; top: 0; width: 370px; height: 100px;
    background: var(--green); border-bottom-left-radius: 26px;
    box-shadow: 0 4px 8px rgba(0,0,0,0.25);
    color: var(--white); text-align: center; padding-top: 14px;
  }
  .contact-tab .phone { font-weight: 700; font-size: 37px; line-height: 1.05; }
  .contact-tab .web { font-weight: 700; font-size: 17px; }
  .program-name {
    position: absolute; left: 64px; top: 46px; display: flex; align-items: center; gap: 14px;
  }
  .program-name .dot { width: 124px; height: 124px; border-radius: 50%; background: var(--green); }
  .program-name .name { font-weight: 700; font-size: 38px; color: var(--ink); line-height: 1.1; width: 300px; }
  .headline {
    position: absolute; left: 0; width: 927px; top: 200px; text-align: center;
    font-weight: 700; font-size: 112px; letter-spacing: 1px; line-height: 1;
    background: linear-gradient(180deg, var(--green-light) 0%, var(--green) 55%, var(--green-dark) 100%);
    -webkit-background-clip: text; background-clip: text; color: transparent;
    padding-left: 84px;
  }
  .subhead {
    position: absolute; left: 288px; top: 306px; font-size: 46px; color: var(--grey); white-space: nowrap;
  }
  .subhead strong { font-weight: 700; }
  .intro {
    position: absolute; left: 434px; top: 398px; width: 440px;
    font-size: 14.5px; line-height: 1.42; color: var(--ink);
  }
  .intro strong { font-weight: 700; }
  .savings { position: absolute; left: 544px; top: 558px; }
  .savings h2 {
    font-family: "Roboto Condensed", "Arial Narrow", sans-serif;
    font-size: 23px; line-height: 1.15; color: var(--green); font-weight: 700; margin-bottom: 10px;
  }
  .benefit-list { list-style: none; }
  .benefit-list li {
    display: flex; align-items: center; gap: 10px; font-size: 18.5px; color: var(--ink); height: 30px;
  }
  .benefit-list svg { width: 20px; height: 20px; flex: none; }
  .price-badge {
    position: absolute; left: 642px; top: 822px; width: 222px; height: 222px;
    border-radius: 50%; background: var(--green);
    box-shadow: 0 4px 10px rgba(0,0,0,0.25);
  }
  .price-badge .inner {
    position: absolute; inset: 0; transform: rotate(-8deg); text-align: center;
    font-family: "Roboto Condensed", "Arial Narrow", sans-serif; font-weight: 700;
    color: var(--white); padding-top: 30px;
  }
  .price-badge .label { color: var(--yellow); font-size: 24px; line-height: 1; padding-left: 40px; }
  .price-badge .amount { font-size: 70px; line-height: 0.95; }
  .price-badge .amount sup { font-size: 42px; vertical-align: 22px; }
  .price-badge .per { font-size: 24px; line-height: 0.9; margin-left: 40px; }
  .price-badge .includes { font-size: 17px; line-height: 1.1; margin-top: 6px; }
  .footer-swoosh { position: absolute; left: 0; top: 960px; width: 927px; height: 240px; }
  .office-mark {
    position: absolute; left: 40px; top: 990px; width: 116px; height: 116px; border-radius: 50%;
    background: var(--white); box-shadow: 0 2px 6px rgba(0,0,0,0.3);
    display: flex; align-items: center; justify-content: center; text-align: center;
    font-weight: 700; font-size: 17px; color: var(--ink); line-height: 1.1; padding: 10px;
  }
  .discount {
    position: absolute; left: 538px; top: 1074px; display: flex; align-items: center; gap: 12px;
    font-family: "Roboto Condensed", "Arial Narrow", sans-serif; font-weight: 700;
  }
  .discount .pct { font-size: 74px; color: var(--yellow); line-height: 1; }
  .discount .text { font-size: 25px; color: var(--white); line-height: 1.1; }
  .address-bar {
    position: absolute; left: 0; bottom: 0; width: 927px; height: 36px; background: var(--green);
    display: flex; align-items: center; padding-left: 54px; gap: 24px;
    font-family: "Roboto Condensed", "Arial Narrow", sans-serif; font-weight: 700; font-size: 15.5px; color: var(--white);
  }
  .address-bar span { display: flex; align-items: center; gap: 12px; white-space: nowrap; }
  .address-bar span::before { content: ""; width: 10px; height: 10px; background: var(--yellow); }
</style>
</head>
<body>
<main class="flyer">
  <div class="family-photo" role="img" aria-label="Photo of a smiling family of four stacked on top of each other on a bed"></div>

  <div class="contact-tab">
    <div class="phone">(801) 563-9071</div>
    <div class="web">www.harborviewdental-example.com</div>
  </div>

  <div class="program-name">
    <span class="dot"></span>
    <span class="name">Careway<br>Benefit Program</span>
  </div>

  <h1 class="headline">JOIN NOW!</h1>
  <p class="subhead">to get your <strong>Dental Benifits</strong></p>

  <p class="intro">Created by local dentists, the Careway Benefit Program is a simple solution for patients without <strong>Dental Insurance.</strong> This one-year membership is offered only to patients of Harborview Dental. Please note: <strong>this plan is not insurance.</strong></p>

  <section class="savings">
    <h2>Start Saving Immediately<br>on your Dental Bills</h2>
    <ul class="benefit-list">
      <li><svg viewBox="0 0 20 20"><path d="M2 11 L8 17 L18 3" fill="none" stroke="#6ab43e" stroke-width="3.5" stroke-linecap="round" stroke-linejoin="round"/></svg>Reduced dental fees</li>
      <li><svg viewBox="0 0 20 20"><path d="M2 11 L8 17 L18 3" fill="none" stroke="#6ab43e" stroke-width="3.5" stroke-linecap="round" stroke-linejoin="round"/></svg>All dependents included</li>
      <li><svg viewBox="0 0 20 20"><path d="M2 11 L8 17 L18 3" fill="none" stroke="#6ab43e" stroke-width="3.5" stroke-linecap="round" stroke-linejoin="round"/></svg>No deductibles or co-pays</li>
      <li><svg viewBox="0 0 20 20"><path d="M2 11 L8 17 L18 3" fill="none" stroke="#6ab43e" stroke-width="3.5" stroke-linecap="round" stroke-linejoin="round"/></svg>Receive your benefit card in days</li>
    </ul>
  </section>

  <svg class="footer-swoosh" viewBox="0 0 927 240" aria-hidden="true">
    <path d="M0 110 C 250 40, 560 40, 927 95 L927 240 L0 240 Z" fill="#6ab43e"/>
    <path d="M0 122 C 250 60, 560 62, 927 108 L927 240 L0 240 Z" fill="#4a4a4c"/>
  </svg>

  <div class="price-badge">
    <div class="inner">
      <div class="label">PLAN COST</div>
      <div class="amount"><sup>$</sup>290</div>
      <div class="per">/person</div>
      <div class="includes">includes 2 cleanings,<br>exams, and x-rays</div>
    </div>
  </div>

  <div class="office-mark">Harborview Dental</div>

  <div class="discount">
    <span class="pct">20%</span>
    <span class="text">Discount off of<br>our standard fees</span>
  </div>

  <footer class="address-bar">
    <span>2718 West 4600 North Suite 209 &nbsp; Salt Lake City, Utah 84157</span>
    <span>Email : info@harborviewdental-example.com</span>
  </footer>
</main>
</body>
</html>
```